Public Adjusters Collective Business card

We need to get business card Design for our Company we are Public Adjusters in Chicago Illinois - i like to see good combination and elements from my Company Logo. as well To be an two side design
Updates

Target Market(s)

Home /Business owner Property Managers

Industry/Entity Type

Business

Contact Information for Business Card

to show the Element of our logo i will Like 3D

Font styles to use
Sans Serif

Requirements
Must have
• Logo and Element of the Logo in 3D
Nice to have
• Logo That we Provide 3D Same Colors or open for suggestions
Should not have
• unleare view -

```html
<!DOCTYPE html>
<html lang="en">
<head>
<meta charset="utf-8">
<title>Public Adjusters Collective – Business Card</title>
<link rel="stylesheet" href="https://fonts.googleapis.com/css2?family=Oswald:wght@400;500&family=Mulish:wght@400;700&display=swap">
<style>
  :root {
    --page: #e9e7e3;
    --navy-deep: #0f1152;
    --navy: #14207a;
    --royal: #0a3fd0;
    --red: #c8070c;
    --white: #ffffff;
    --brand-blue: #1f3aa8;
    --rule: rgba(255,255,255,0.35);
  }
  * { box-sizing: border-box; margin: 0; padding: 0; }
  html, body { width: 1200px; height: 987px; overflow: hidden; }
  body { background: var(--page); position: relative; font-family: "Mulish", sans-serif; }

  .card {
    position: absolute;
    left: 293px;
    width: 615px;
    height: 351px;
    overflow: hidden;
    box-shadow: 0 3px 10px rgba(0,0,0,0.25);
  }
  .card--front { top: 130px; }
  .card--back  { top: 506px; }

  .card__bg { position: absolute; inset: 0; width: 100%; height: 100%; }

  .brand {
    position: absolute;
    left: 20px; width: 260px;
    top: 34px;
    display: flex; flex-direction: column; align-items: center; gap: 30px;
  }
  .brand__dot {
    width: 96px; height: 96px; border-radius: 50%;
    background: var(--brand-blue);
  }
  .brand__name {
    font-family: "Mulish", sans-serif;
    font-weight: 700;
    font-size: 16px;
    line-height: 20px;
    color: var(--brand-blue);
    white-space: nowrap;
  }

  .person {
    position: absolute; right: 31px; top: 20px; text-align: right; color: var(--white);
  }
  .person__name {
    font-family: "Oswald", sans-serif; font-weight: 500;
    font-size: 31px; line-height: 38px; letter-spacing: 0.5px;
  }
  .person__title {
    font-family: "Oswald", sans-serif; font-weight: 400;
    font-size: 19px; line-height: 22px; letter-spacing: 0.3px;
  }

  .address {
    position: absolute; right: 31px; top: 157px;
    text-align: right; color: var(--white);
    font-size: 16px; line-height: 21px; font-style: normal;
  }

  .contacts {
    position: absolute; right: 33px; top: 212px;
    list-style: none; color: var(--white);
    font-size: 16px; line-height: 23.4px;
  }
  .contacts li { display: flex; justify-content: flex-end; align-items: center; gap: 10px; }
  .contacts svg { width: 16px; height: 16px; flex: none; }

  .back-brand {
    position: absolute; left: 0; right: 0; top: 92px;
    display: flex; flex-direction: column; align-items: center; gap: 18px;
  }
  .back-brand__dot {
    width: 100px; height: 100px; border-radius: 50%;
    background: var(--white);
  }
  .back-brand__name {
    font-family: "Mulish", sans-serif; font-weight: 700;
    font-size: 20px; line-height: 24px; color: var(--white);
  }
  .back-rule {
    position: absolute; left: 88px; width: 439px; top: 270px; height: 1px;
    background: linear-gradient(90deg, transparent, var(--rule) 20%, var(--rule) 80%, transparent);
  }
  .back-url {
    position: absolute; left: 0; right: 0; top: 284px;
    text-align: center; color: var(--white);
    font-size: 16px; line-height: 20px; letter-spacing: 2.4px;
  }
</style>
</head>
<body>

  <section class="card card--front" aria-label="Business card front">
    <svg class="card__bg" viewBox="0 0 615 351" preserveAspectRatio="none" aria-hidden="true">
      <defs>
        <radialGradient id="frontGlow" cx="0.72" cy="0.42" r="0.6">
          <stop offset="0" stop-color="#0a48e0"/>
          <stop offset="0.55" stop-color="#122b9a"/>
          <stop offset="1" stop-color="#0f1152"/>
        </radialGradient>
      </defs>
      <rect width="615" height="351" fill="url(#frontGlow)"/>
      <path d="M348,60 C348,200 300,300 210,351 H122 C235,305 335,215 348,60 Z" fill="#c8070c"/>
      <path d="M0,0 H340 C352,130 300,270 205,351 H0 Z" fill="#ffffff"/>
    </svg>

    <div class="brand">
      <span class="brand__dot" aria-hidden="true"></span>
      <span class="brand__name">Public Adjusters Collective</span>
    </div>

    <div class="person">
      <p class="person__name">DANIEL REYES</p>
      <p class="person__title">CEO/Founder</p>
    </div>

    <address class="address">
      2140 Lakeview Court<br>
      Chicago, Illinois 60614
    </address>

    <ul class="contacts">
      <li>312 555 0147
        <svg viewBox="0 0 16 16" aria-hidden="true"><path fill="#fff" d="M3.5 1.5l2.5 0 1 3.5-1.6 1.2c.8 1.7 2.1 3 3.8 3.8L10.4 8.4l3.6 1v2.6c0 .8-.7 1.5-1.5 1.5C6.7 13.5 2 8.8 2 3c0-.8.7-1.5 1.5-1.5z"/></svg>
      </li>
      <li>312 555 0182
        <svg viewBox="0 0 16 16" aria-hidden="true"><rect x="4" y="1" width="8" height="14" rx="1.5" fill="none" stroke="#fff" stroke-width="1.6"/><circle cx="8" cy="12.5" r="0.9" fill="#fff"/></svg>
      </li>
      <li>312 555 0139
        <svg viewBox="0 0 16 16" aria-hidden="true"><rect x="4" y="1.5" width="8" height="4" fill="#fff"/><rect x="1" y="6" width="14" height="6" rx="1" fill="#fff"/><rect x="4" y="10" width="8" height="4.5" fill="#fff" stroke="#14207a" stroke-width="0.8"/></svg>
      </li>
      <li>hello@pacollective.com
        <svg viewBox="0 0 16 16" aria-hidden="true"><rect x="1.5" y="3.5" width="13" height="9" fill="#fff"/><path d="M1.5 3.5 L8 9 L14.5 3.5" fill="none" stroke="#14207a" stroke-width="1.2"/></svg>
      </li>
      <li>www.pacollective.com
        <svg viewBox="0 0 16 16" aria-hidden="true"><circle cx="8" cy="8" r="6.5" fill="#fff"/><ellipse cx="8" cy="8" rx="2.6" ry="6.5" fill="none" stroke="#14207a" stroke-width="1"/><path d="M1.5 8h13" stroke="#14207a" stroke-width="1"/></svg>
      </li>
    </ul>
  </section>

  <section class="card card--back" aria-label="Business card back">
    <svg class="card__bg" viewBox="0 0 615 351" preserveAspectRatio="none" aria-hidden="true">
      <defs>
        <radialGradient id="backGlow" cx="0.5" cy="0.42" r="0.62">
          <stop offset="0" stop-color="#0a48e0"/>
          <stop offset="0.5" stop-color="#122b9a"/>
          <stop offset="1" stop-color="#0f1152"/>
        </radialGradient>
      </defs>
      <rect width="615" height="351" fill="url(#backGlow)"/>
    </svg>

    <div class="back-brand">
      <span class="back-brand__dot" aria-hidden="true"></span>
      <span class="back-brand__name">Public Adjusters Collective</span>
    </div>
    <div class="back-rule" aria-hidden="true"></div>
    <p class="back-url">www.PublicAdjustersCollective.com</p>
  </section>

</body>
</html>
```